KLV Plant Services

We are a heavy diesel mechanical business with additional air con certificates, remapping engine rebuilt

Contact Information for Business Card

Company Name, Director Name, Managing Director, Contact details, email and website

Font styles to use
Serif
Script

```html
<!DOCTYPE html>
<html lang="en">
<head>
<meta charset="utf-8">
<title>KLV Plant Services – Business Card</title>
<link rel="stylesheet" href="https://fonts.googleapis.com/css2?family=Josefin+Sans:wght@300;400;600;700&display=swap">
<style>
  :root {
    --stage: #3a3a3c;
    --card: #f7f7f7;
    --card-shade: #ebebeb;
    --navy: #2b2a6e;
    --ink: #111111;
    --grey-text: #6b6b6b;
    --rule: #6f6da3;
    --ghost: #dedede;
  }
  * { box-sizing: border-box; margin: 0; padding: 0; }
  html, body { width: 1200px; height: 900px; overflow: hidden; }
  body {
    background: var(--stage);
    font-family: "Josefin Sans", sans-serif;
    position: relative;
  }
  .card {
    position: absolute;
    left: 250px;
    width: 700px;
    height: 400px;
    border-radius: 34px;
    background: linear-gradient(135deg, var(--card) 0%, var(--card) 55%, var(--card-shade) 100%);
    overflow: hidden;
  }
  .card--front { top: 36px; }
  .card--back { top: 464px; }

  .ghost-arm {
    position: absolute;
    right: 70px;
    top: 0;
    width: 150px;
    height: 230px;
    border-radius: 0 0 60px 20px;
    background: linear-gradient(180deg, rgba(222,222,222,0.6) 0%, var(--ghost) 100%);
  }

  .brand {
    position: absolute;
    display: flex;
    align-items: center;
    gap: 14px;
    color: var(--navy);
    font-weight: 700;
    font-size: 34px;
    line-height: 1;
  }
  .brand__dot {
    width: 26px;
    height: 26px;
    border-radius: 50%;
    background: var(--navy);
    flex: none;
  }
  .card--front .brand { left: 60px; top: 130px; }
  .card--back .brand { left: 60px; top: 120px; }

  .website {
    position: absolute;
    right: 60px;
    bottom: 120px;
    font-weight: 700;
    font-size: 17px;
    letter-spacing: 0.32em;
    color: var(--ink);
  }

  .details {
    position: absolute;
    left: 60px;
    right: 50px;
    bottom: 42px;
  }
  .details__rule {
    height: 1px;
    background: var(--rule);
    margin-bottom: 12px;
  }
  .details__top {
    display: flex;
    align-items: baseline;
    gap: 10px;
    margin-bottom: 10px;
  }
  .person {
    font-weight: 700;
    font-size: 24px;
    color: var(--navy);
    letter-spacing: 0.02em;
  }
  .role {
    font-weight: 300;
    font-size: 17px;
    color: var(--grey-text);
    border-left: 2px solid var(--navy);
    padding-left: 10px;
  }
  .email {
    margin-left: auto;
    font-size: 15px;
    color: var(--grey-text);
  }
  .phone {
    font-size: 17px;
    color: var(--navy);
    margin-bottom: 8px;
    letter-spacing: 0.04em;
  }
  .address {
    font-size: 16px;
    color: var(--grey-text);
  }
</style>
</head>
<body>
  <section class="card card--front">
    <div class="ghost-arm" role="img" aria-label="Faint excavator arm and bucket decoration"></div>
    <div class="brand"><span class="brand__dot"></span>KLV Plant Services</div>
    <p class="website">www.klvplantservices.net</p>
  </section>

  <section class="card card--back">
    <div class="ghost-arm" role="img" aria-label="Faint excavator arm and bucket decoration"></div>
    <div class="brand"><span class="brand__dot"></span>KLV Plant Services</div>
    <div class="details">
      <div class="details__top">
        <span class="person">DEAN HARLOW</span>
        <span class="role">Managing Director</span>
        <span class="email">admin@klvplantservices.net</span>
      </div>
      <div class="details__rule"></div>
      <p class="phone">T. 0412 555 308</p>
      <p class="address">48 Carrow Street, Maylands, WA 6051, Australia</p>
    </div>
  </section>
</body>
</html>
```